Website for Life Strategies business

We need a website to present our video, audio and print content to subcribers at Bright Summit Mentors. We will offer a team of coaches who can help people breakthrough the barriers that keep them from reaching their physical, spiritual, financial, leadership and relationship goals.

Target Market(s)

Anyone who needs help with strategies to take their life to a new level of success.

Industry/Entity Type

Life Coaching

Logo Text

Bright Summit Mentors

Number of Pages Required

5+ page

Colors

Designer to choose colors to be used in the design.

Requirements
Must have
• The ability to present content as a package that includes Word Documents, videos and audio content as well as to be able to display books for sale. Each week their would be a new package for subscribers to access. It should provide the ability for subscribers to comment on the material and share how their lives were changed by the content. Should also include a shop page to offer merchandise for sale.
Nice to have
• Not sure
Should not have
• Not sure

```html
<!DOCTYPE html>
<html lang="en">
<head>
<meta charset="utf-8">
<title>Bright Summit Mentors</title>
<link rel="stylesheet" href="https://fonts.googleapis.com/css2?family=Roboto+Slab:wght@300;400&family=Roboto:wght@400;500;700&display=swap">
<style>
:root{
  --green:#8dc63f;
  --green-soft:#9acd5c;
  --blue:#29b6f6;
  --ink:#444;
  --muted:#6f6f6f;
  --pale:#f5f6f8;
  --footer:#2b2b2b;
  --white:#fff;
}
*{margin:0;padding:0;box-sizing:border-box}
html,body{width:1200px;height:2253px;overflow:hidden;background:var(--white)}
body{position:relative;font-family:"Roboto",sans-serif;color:var(--ink)}
.abs{position:absolute}
.slab{font-family:"Roboto Slab",serif}

/* header */
.site-header{left:0;top:0;width:1200px;height:87px;background:var(--white);box-shadow:0 1px 3px rgba(0,0,0,.08);z-index:2}
.brand{left:85px;top:30px;font-family:"Roboto Slab",serif;font-size:22px;color:#444;font-weight:400}
.main-nav a{position:absolute;top:38px;font-size:11.5px;font-weight:500;color:#444;text-decoration:none;text-transform:uppercase}
.main-nav a.active{color:var(--green)}
.search-btn{left:1069px;top:22px;width:45px;height:45px;border:2px solid var(--green);border-radius:50%}

/* hero */
.hero{left:0;top:87px;width:1200px;height:513px;background:linear-gradient(90deg,#eef2f3 0%,#dfe6ea 38%,#7d8b99 60%,#34435a 78%,#233048 100%)}
.hero-kicker{left:85px;top:234px;font-family:"Roboto Slab",serif;font-size:38px;color:var(--green);font-weight:300}
.hero-title{left:85px;top:292px;font-family:"Roboto Slab",serif;font-size:31px;color:#444}
.hero-text{left:85px;top:352px;width:400px;font-size:12.5px;line-height:24px;color:#555}
.btn{position:absolute;height:42px;color:var(--white);font-family:"Roboto Slab",serif;font-size:14px;line-height:42px;text-align:center;border-radius:2px}
.btn-green{background:var(--green-soft)}
.btn-blue{background:var(--blue)}
.dot{top:574px;width:12px;height:12px;border:1.5px solid #555;border-radius:50%}
.dot.on{border-color:var(--green)}

/* welcome */
.center{left:0;width:1200px;text-align:center}
.welcome-over{top:646px;font-family:"Roboto Slab",serif;font-size:20px;color:#444}
.welcome-title{top:678px;font-family:"Roboto Slab",serif;font-size:28px;color:var(--green);font-weight:300}
.welcome-text{left:200px;top:730px;width:800px;text-align:center;font-size:12px;line-height:23.5px;color:#666}

/* coaches */
.coaches{left:0;top:902px;width:1200px;height:428px;background:var(--pale)}
.section-title{font-family:"Roboto Slab",serif;font-size:20px;color:var(--green)}
.coach{top:1036px;width:240px;text-align:center}
.coach-icon{width:114px;height:114px;margin:0 auto;border-radius:50%;background:var(--green-soft);display:flex;align-items:center;justify-content:center}
.coach-name{margin-top:18px;font-family:"Roboto Slab",serif;font-size:19px;color:var(--green)}
.coach-text{margin-top:8px;font-size:12px;line-height:23px;color:#666}

/* featured */
.feature-title{left:85px;top:1382px;font-family:"Roboto Slab",serif;font-size:21px;color:var(--green)}
.feature-text{left:85px;width:450px;font-size:12px;line-height:25.5px;color:#777}
.feature-link{left:85px;top:1668px;font-family:"Roboto Slab",serif;font-size:13px;color:var(--green);text-decoration:underline}
.video-frame{left:593px;top:1372px;width:520px;height:310px;background:linear-gradient(135deg,#d9dcdf,#b9bfc6 55%,#8f99a4)}
.play{left:816px;top:1491px;width:72px;height:72px;border:2px solid var(--white);border-radius:50%}

/* testimonial */
.testimonial{left:0;top:1728px;width:1200px;height:290px;background:linear-gradient(135deg,#97cb5a,#8fc550 50%,#9bce60)}
.quote-text{left:176px;top:1800px;width:530px;font-size:12px;line-height:23.5px;color:var(--white)}
.quote-mark{font-family:"Roboto Slab",serif;font-size:32px;color:var(--white)}
.author{left:176px;top:1917px;font-size:14px;font-weight:700;color:var(--white)}
.posted{left:176px;top:1941px;font-size:12px;color:var(--white)}
.portrait{left:773px;top:1768px;width:196px;height:196px;border-radius:50%;border:5px solid #f3f3f3;background:linear-gradient(160deg,#c9a88c,#8a6450)}

/* footer */
.site-footer{left:0;top:2018px;width:1200px;height:235px;background:var(--footer)}
.social{top:2051px;width:60px;height:60px;border:1.5px solid #ddd;border-radius:50%;display:flex;align-items:center;justify-content:center}
.footer-rule{left:85px;top:2126px;width:1028px;height:1px;background:#444}
.footer-nav{top:2150px;font-size:11.5px;color:#eee;word-spacing:0}
.footer-nav span{margin:0 20px}
.copyright{top:2192px;font-size:11.5px;color:#ddd}
</style>
</head>
<body>

<header class="abs site-header">
  <div class="abs brand">Bright Summit Mentors</div>
  <nav class="main-nav">
    <a class="active" style="left:537px">Home</a>
    <a style="left:617px">About Us</a>
    <a style="left:722px">Services</a>
    <a style="left:825px">News</a>
    <a style="left:906px">Video</a>
    <a style="left:988px">Contact Us</a>
  </nav>
  <div class="abs search-btn">
    <svg width="41" height="41" viewBox="0 0 41 41"><circle cx="19.5" cy="19.5" r="3.5" fill="none" stroke="#8dc63f" stroke-width="1.6"/><line x1="22" y1="22" x2="25" y2="25" stroke="#8dc63f" stroke-width="1.6"/></svg>
  </div>
</header>

<section class="abs hero" role="img" aria-label="Photo of two businessmen reviewing a tablet in a bright office"></section>
<div class="abs hero-kicker">BRIGHT SUMMIT</div>
<div class="abs hero-title">MENTORS</div>
<p class="abs hero-text">Sed ut perspiciatis unde omnis iste natus error sit voluptatem accusan-tium doloremque laudantium, totam rem aperiam, eaque ipsa quae ab illo quasi architecto beatae vitae dicta sunt explicabo.</p>
<div class="btn btn-green" style="left:85px;top:446px;width:130px">READ MORE</div>
<div class="abs dot" style="left:85px"></div>
<div class="abs dot on" style="left:103px"></div>
<div class="abs dot" style="left:121px"></div>

<section>
  <div class="abs center welcome-over">WELCOME TO</div>
  <h1 class="abs center welcome-title" style="font-weight:300">BRIGHT SUMMIT MENTORS</h1>
  <p class="abs welcome-text">Sed ut perspiciatis unde omnis iste natus error sit voluptatem accusantium doloremque laudantium, totam rem aperiam, eaque ipsa quae ab illo inventore veritatis et quasi architecto beatae vitae dicta sunt explicabo. Nemo enim ipsam voluptatem quia voluptas sit aspernatur aut odit aut fugit, sed quia consequuntur magni dolores eos qui ratione voluptatem sequi nesciunt.</p>
  <div class="btn btn-green" style="left:465px;top:824px;width:131px">READ MORE</div>
  <div class="btn btn-blue" style="left:603px;top:824px;width:131px">AUDIO &amp; PRINT</div>
</section>

<section class="abs coaches"></section>
<h2 class="abs center section-title" style="top:936px;font-weight:400">OUR COACHES</h2>
<p class="abs center" style="top:972px;font-size:12px;color:#666">Sed ut perspiciatis unde omnis iste natus error sit voluptatem accusantium doloremque laudantium, totam rem aperiam,</p>

<div class="abs coach" style="left:89px">
  <div class="coach-icon"><svg width="50" height="50" viewBox="0 0 50 50"><circle cx="25" cy="25" r="18" fill="none" stroke="#fff" stroke-width="4"/><path d="M25 14v11l8 6" fill="none" stroke="#fff" stroke-width="4" stroke-linecap="round"/></svg></div>
  <div class="coach-name">Physical</div>
  <p class="coach-text">Sed ut perspiciatis unde omnis iste natus aperiam, eaque ipsa quae ab illo invenvi-tae dicta sunt explicabo.</p>
</div>
<div class="abs coach" style="left:350px">
  <div class="coach-icon"><svg width="50" height="50" viewBox="0 0 50 50"><path d="M25 42C10 32 6 24 6 17a9 9 0 0 1 19-4 9 9 0 0 1 19 4c0 7-4 15-19 25z" fill="#fff"/></svg></div>
  <div class="coach-name">Spiritual</div>
  <p class="coach-text">Sed ut perspiciatis unde omnis iste natus aperiam, eaque ipsa quae ab illo invenvi-tae dicta sunt explicabo.</p>
</div>
<div class="abs coach" style="left:610px">
  <div class="coach-icon"><svg width="56" height="56" viewBox="0 0 56 56"><rect x="8" y="36" width="7" height="12" fill="#fff"/><rect x="19" y="30" width="7" height="18" fill="#fff"/><rect x="30" y="24" width="7" height="24" fill="#fff"/><rect x="41" y="16" width="7" height="32" fill="#fff"/><path d="M8 28l12-8 10 4 14-14" fill="none" stroke="#fff" stroke-width="3"/></svg></div>
  <div class="coach-name">Financial</div>
  <p class="coach-text">Sed ut perspiciatis unde omnis iste natus aperiam, eaque ipsa quae ab illo invenvi-tae dicta sunt explicabo.</p>
</div>
<div class="abs coach" style="left:870px">
  <div class="coach-icon"><svg width="56" height="50" viewBox="0 0 56 50"><circle cx="12" cy="14" r="6" fill="#fff"/><circle cx="28" cy="10" r="7" fill="#fff"/><circle cx="44" cy="14" r="6" fill="#fff"/><rect x="5" y="23" width="14" height="20" rx="4" fill="#fff"/><rect x="20" y="20" width="16" height="26" rx="4" fill="#fff"/><rect x="37" y="23" width="14" height="20" rx="4" fill="#fff"/></svg></div>
  <div class="coach-name">Leadership</div>
  <p class="coach-text">Sed ut perspiciatis unde omnis iste natus aperiam, eaque ipsa quae ab illo invenvi-tae dicta sunt explicabo.</p>
</div>

<section>
  <h2 class="abs feature-title" style="font-weight:400">FEATURED VIDEO</h2>
  <p class="abs feature-text" style="top:1422px">Sed ut perspiciatis unde omnis iste natus error sit voluptatem accusantium dolorem que laudantium, totam rem aperiam, eaque ipsa quae ab illo inventore veritatis et quasi architecto beatae vitae dicta sunt explicabo. Nemo enim ipsam voluptatem qu ia voluptas sit aspernatur aut odit aut fugit, sed quia consequuntur magni dolores eo qui ratione voluptatem sequi nesciunt.</p>
  <p class="abs feature-text" style="top:1568px">Nemo enim ipsam voluptatem qu ia voluptas sit aspernatur aut odit aut fugit, sed quia consequuntur magni dolores eo qui ratione voluptatem sequi nesciunt. Neque porro quisquam est, qui dolorem con sectetur…</p>
  <a class="abs feature-link">READ MORE</a>
  <div class="abs video-frame" role="img" aria-label="Video still of a team meeting around a white table with charts"></div>
  <div class="abs play"><svg width="68" height="68" viewBox="0 0 68 68"><path d="M28 22l18 12-18 12z" fill="#fff"/></svg></div>
</section>

<section class="abs testimonial"></section>
<div class="abs quote-mark" style="left:156px;top:1772px">&ldquo;</div>
<p class="abs quote-text">Sed ut perspiciatis unde omnis iste natus error sit voluptatem accusantium doloremque laudantium, totam rem aperiam, eaque ipsa quae ab illo inventore veritatis et quasi architecto beatae vitae dicta sunt explicabo. Nemo enim ipsam voluptatem quia voluptas sit aspernatur aut odit aut fugit, sed quia consequuntur magni dolores eos qui ratione voluptatem sequi nesciunt.</p>
<div class="abs quote-mark" style="left:560px;top:1876px">&rdquo;</div>
<div class="abs author">DANA MILLS</div>
<div class="abs posted">Posted On 07 May 2017</div>
<div class="abs portrait" role="img" aria-label="Portrait photo of a smiling client"></div>
<svg class="abs" style="left:46px;top:1822px" width="18" height="84" viewBox="0 0 18 84"><path d="M16 2L2 42l14 40" fill="none" stroke="rgba(255,255,255,.6)" stroke-width="2"/></svg>
<svg class="abs" style="left:1136px;top:1822px" width="18" height="84" viewBox="0 0 18 84"><path d="M2 2l14 40L2 82" fill="none" stroke="rgba(255,255,255,.6)" stroke-width="2"/></svg>

<footer class="abs site-footer"></footer>
<div class="abs social" style="left:390px" aria-label="Social link"></div>
<div class="abs social" style="left:463px" aria-label="Social link"></div>
<div class="abs social" style="left:536px" aria-label="Social link"></div>
<div class="abs social" style="left:606px" aria-label="Social link"></div>
<div class="abs social" style="left:676px" aria-label="Social link"></div>
<div class="abs social" style="left:748px" aria-label="Email">
  <svg width="16" height="12" viewBox="0 0 16 12"><rect x="1" y="1" width="14" height="10" rx="1" fill="none" stroke="#fff" stroke-width="1.5"/><path d="M1 2l7 5 7-5" fill="none" stroke="#fff" stroke-width="1.5"/></svg>
</div>
<div class="abs footer-rule"></div>
<nav class="abs center footer-nav">HOME<span>|</span>ABOUT US<span>|</span>SERVICES<span>|</span>NEWS<span>|</span>VIDEO<span>|</span>CONTACT US</nav>
<div class="abs center copyright">© Copyrights 2017 Bright Summit Mentors.All Rights Reserved.</div>

</body>
</html>
```